Business Card for Lantern Reach

Please design a Modern Business card for a Online Marketing Company

Website: http://www.lanternreach-example.com.au

Please do NOT include physical address in design.

```html
<!DOCTYPE html>
<html lang="en">
<head>
<meta charset="utf-8">
<title>Lantern Reach — Business Card</title>
<link rel="stylesheet" href="https://fonts.googleapis.com/css2?family=Open+Sans:wght@400;600&display=swap">
<style>
  :root {
    --stage: #4a2f1d;
    --card-dark: #050505;
    --card-light: #ffffff;
    --brand-red: #b8141f;
    --accent-orange: #f28c1b;
    --text-light: #f2f2f2;
    --text-dark: #2b2b2b;
  }
  * { box-sizing: border-box; margin: 0; padding: 0; }
  html, body { width: 1200px; height: 466px; overflow: hidden; }
  body {
    background: var(--stage);
    font-family: "Open Sans", Arial, sans-serif;
    position: relative;
  }
  .card {
    position: absolute;
    top: 88px;
    width: 520px;
    height: 290px;
    border-radius: 22px;
    overflow: hidden;
  }
  .card--front { left: 50px; background: var(--card-dark); }
  .card--back { left: 630px; background: var(--card-light); }

  .brand-name {
    font-family: "Open Sans", Arial, sans-serif;
    font-weight: 600;
    color: var(--brand-red);
    line-height: 1.1;
  }
  .tagline {
    font-family: "Open Sans", Arial, sans-serif;
    font-weight: 600;
    line-height: 1.2;
  }

  /* front */
  .front-brand { position: absolute; left: 36px; top: 44px; }
  .front-brand .brand-name { font-size: 26px; }
  .front-brand .tagline { font-size: 12px; color: var(--text-light); margin-top: 4px; }

  .person { position: absolute; left: 36px; top: 150px; }
  .person-name { color: var(--accent-orange); font-size: 19px; font-weight: 600; line-height: 1.2; }
  .person-title { color: var(--text-light); font-size: 14px; line-height: 1.3; }
  .contact-list { list-style: none; margin-top: 10px; }
  .contact-item {
    display: flex; align-items: center; gap: 8px;
    color: var(--text-light); font-size: 12.5px; line-height: 1.6;
  }
  .contact-icon { width: 12px; height: 12px; flex: none; }

  /* back */
  .back-brand {
    position: absolute; left: 0; right: 0; top: 98px;
    text-align: center;
  }
  .back-brand .brand-name { font-size: 38px; }
  .back-brand .tagline { font-size: 15px; color: var(--text-dark); margin-top: 6px; }
  .back-url {
    position: absolute; left: 0; right: 0; bottom: 56px;
    text-align: center; font-size: 19px; color: var(--text-dark); letter-spacing: 0.3px;
  }
</style>
</head>
<body>
  <section class="card card--front" aria-label="Card front">
    <div class="front-brand">
      <div class="brand-name">Lantern Reach</div>
      <div class="tagline">Be seen online - Grow online</div>
    </div>
    <div class="person">
      <div class="person-name">Your Name</div>
      <div class="person-title">Title</div>
      <ul class="contact-list">
        <li class="contact-item">
          <svg class="contact-icon" viewBox="0 0 12 12" aria-hidden="true"><path fill="#f28c1b" d="M2.5 1h2l.8 2.5-1.3 1a6 6 0 0 0 3 3l1-1.3L11 7v2c0 1-1 2-2 2A8 8 0 0 1 1 3c0-1 .7-2 1.5-2z"/></svg>
          <span>0400 555 019</span>
        </li>
        <li class="contact-item">
          <svg class="contact-icon" viewBox="0 0 12 12" aria-hidden="true"><rect x="0.5" y="2.5" width="11" height="7.5" rx="1" fill="#f28c1b"/><path d="M1 3l5 4 5-4" fill="none" stroke="#050505" stroke-width="1"/></svg>
          <span>plan@lanternreach-example.com.au</span>
        </li>
        <li class="contact-item">
          <svg class="contact-icon" viewBox="0 0 12 12" aria-hidden="true"><circle cx="6" cy="6" r="5.3" fill="#f28c1b"/><g fill="none" stroke="#050505" stroke-width="0.8"><ellipse cx="6" cy="6" rx="2.3" ry="5.3"/><path d="M0.7 6h10.6M1.5 3.5h9M1.5 8.5h9"/></g></svg>
          <span>www.lanternreach-example.com.au</span>
        </li>
      </ul>
    </div>
  </section>

  <section class="card card--back" aria-label="Card back">
    <div class="back-brand">
      <div class="brand-name">Lantern Reach</div>
      <div class="tagline">Be seen online - Grow online</div>
    </div>
    <div class="back-url">www.lanternreach-example.com.au</div>
  </section>
</body>
</html>
```